Book Cover for Lanterns Along the Quiet Threshold

I need a book cover for a 6 x 9 paperback titled Lanterns Along the Quiet Threshold Gathered from Research and Voices Dwelling in the Realm beyond Our Present Days. It has to do with consciousness, the mind, incarnation onto Earth, leaving Earth, and the life in the life after this life. I have an idea I'm providing with this description, but I am open to anything that would be striking and stimulating, whether with a book or not. I am the author, T. Morgan Wexley. I've added another background idea to see if anyone can do something with it and I've increased the budget.

```html
<!DOCTYPE html>
<html lang="en">
<head>
<meta charset="utf-8">
<title>Lanterns Along the Quiet Threshold — Book Cover</title>
<link href="https://fonts.googleapis.com/css2?family=Playfair+Display:wght@400;700;900&family=Cormorant+Garamond:wght@500;600&display=swap" rel="stylesheet">
<style>
  :root {
    --page: #ffffff;
    --spine-leather: #8b4a27;
    --spine-leather-dark: #6e3519;
    --panel-leather: #5a2216;
    --panel-leather-light: #74301f;
    --corner-leather: #61281b;
    --strap: #1d1a19;
    --strap-edge: #3a3330;
    --border-band: #c7792a;
    --border-band-dark: #8f4e17;
    --gold: #c8a54c;
    --gold-deep: #9c7a2c;
    --divider: #6b6361;
  }
  * { margin: 0; padding: 0; box-sizing: border-box; }
  html, body {
    width: 1200px; height: 1200px; overflow: hidden; background: var(--page);
  }
  .canvas { position: relative; width: 1200px; height: 1200px; }
  .cover {
    position: absolute; left: 300px; top: 150px; width: 600px; height: 900px;
    box-shadow: 0 4px 14px rgba(0,0,0,0.25);
  }
  .cover-shapes { position: absolute; inset: 0; }
  .cover-text {
    position: absolute; left: 170px; width: 360px; text-align: center;
    color: var(--gold);
    text-shadow: 0 1px 0 var(--gold-deep), 0 2px 3px rgba(0,0,0,0.55);
    white-space: nowrap;
  }
  .title-main {
    top: 146px;
    font-family: "Playfair Display", serif; font-weight: 900;
    font-size: 54px; letter-spacing: 2px; line-height: 1;
  }
  .title-lead {
    top: 342px;
    font-family: "Playfair Display", serif; font-weight: 700;
    font-size: 25px; letter-spacing: 1.5px; line-height: 1;
  }
  .title-tail {
    top: 374px;
    font-family: "Playfair Display", serif; font-weight: 900;
    font-size: 52px; letter-spacing: 2px; line-height: 1;
  }
  .subtitle {
    top: 512px;
    font-family: "Cormorant Garamond", serif; font-weight: 600;
    font-size: 11px; letter-spacing: 2.5px; line-height: 20px;
    text-transform: uppercase; text-shadow: 0 1px 2px rgba(0,0,0,0.5);
  }
  .author {
    top: 764px;
    font-family: "Cormorant Garamond", serif; font-weight: 500;
    font-size: 22px; letter-spacing: 4px; line-height: 1;
    text-transform: uppercase; text-shadow: 0 1px 2px rgba(0,0,0,0.5);
  }
</style>
</head>
<body>
<div class="canvas">
  <div class="cover">
    <svg class="cover-shapes" width="600" height="900" viewBox="0 0 600 900" xmlns="http://www.w3.org/2000/svg">
      <defs>
        <radialGradient id="panelTone" cx="50%" cy="50%" r="70%">
          <stop offset="0" stop-color="var(--panel-leather-light)"/>
          <stop offset="1" stop-color="var(--panel-leather)"/>
        </radialGradient>
        <linearGradient id="spineTone" x1="0" x2="1">
          <stop offset="0" stop-color="var(--spine-leather-dark)"/>
          <stop offset="0.4" stop-color="var(--spine-leather)"/>
          <stop offset="1" stop-color="var(--spine-leather-dark)"/>
        </linearGradient>
        <linearGradient id="goldTone" x1="0" x2="1" y1="0" y2="1">
          <stop offset="0" stop-color="#e2c676"/>
          <stop offset="1" stop-color="#a9862f"/>
        </linearGradient>
      </defs>

      <rect class="front-panel" x="150" y="0" width="450" height="900" fill="url(#panelTone)"/>

      <rect class="border-band" x="156" y="27" width="272" height="22" fill="var(--border-band)" stroke="var(--border-band-dark)" stroke-width="2"/>
      <rect class="border-band" x="551" y="178" width="22" height="530" fill="var(--border-band)" stroke="var(--border-band-dark)" stroke-width="2"/>
      <rect class="border-band" x="156" y="831" width="272" height="22" fill="var(--border-band)" stroke="var(--border-band-dark)" stroke-width="2"/>

      <polygon class="corner-guard" points="400,0 600,0 600,205 580,205" fill="var(--corner-leather)" stroke="#3e160d" stroke-width="2"/>
      <polygon class="corner-guard" points="600,695 600,900 400,900 580,695" fill="var(--corner-leather)" stroke="#3e160d" stroke-width="2"/>
      <rect role="img" aria-label="Embossed floral flourish on corner guard" x="520" y="25" width="60" height="110" fill="#54200f" opacity="0.6"/>
      <rect role="img" aria-label="Embossed floral flourish on corner guard" x="520" y="770" width="60" height="110" fill="#54200f" opacity="0.6"/>

      <rect class="spine" x="0" y="0" width="150" height="900" fill="url(#spineTone)"/>
      <rect class="spine-divider" x="150" y="0" width="6" height="900" fill="var(--divider)"/>

      <rect class="spine-band" x="0" y="225" width="150" height="75" fill="#7b3c1f" stroke="#4a210f" stroke-width="2"/>
      <rect class="spine-band" x="0" y="599" width="150" height="75" fill="#7b3c1f" stroke="#4a210f" stroke-width="2"/>
      <circle class="rivet" cx="60" cy="262" r="18" fill="url(#goldTone)"/>
      <circle class="rivet" cx="110" cy="262" r="18" fill="url(#goldTone)"/>
      <circle class="rivet" cx="60" cy="636" r="18" fill="url(#goldTone)"/>
      <circle class="rivet" cx="110" cy="636" r="18" fill="url(#goldTone)"/>

      <rect class="strap" x="156" y="227" width="444" height="71" fill="var(--strap)" stroke="var(--strap-edge)" stroke-width="2"/>
      <rect class="strap" x="156" y="601" width="444" height="71" fill="var(--strap)" stroke="var(--strap-edge)" stroke-width="2"/>
      <ellipse class="buckle" cx="533" cy="263" rx="38" ry="50" fill="none" stroke="#8f7a4a" stroke-width="5"/>
      <ellipse class="buckle" cx="533" cy="637" rx="38" ry="50" fill="none" stroke="#8f7a4a" stroke-width="5"/>

      <rect role="img" aria-label="Antique brass skeleton key" x="56" y="356" width="56" height="186" rx="6" fill="url(#goldTone)" opacity="0.85"/>
    </svg>

    <div class="cover-text title-main">LANTERNS</div>
    <div class="cover-text title-lead">Along the Quiet</div>
    <div class="cover-text title-tail">Threshold</div>
    <div class="cover-text subtitle">Gathered from Research<br>and Voices Dwelling in the Realm<br>beyond Our Present Days</div>
    <div class="cover-text author">T. Morgan Wexley</div>
  </div>
</div>
</body>
</html>
```